Business Card Design Project

I am opening a skin care studio called Glow Haven by Marisol. I will be offering a wide range of unique and affordable skin services including facials, chemical peels, microdermabrasion treatments, body wraps, salt glows, all waxing and eye lash extensions. If the business cards depicts what I would like, this would lead to brochures, web design, signs, etc.

Project Deadline Extended
Reason: A request to extend deadline was requested. I will be more than happy to accommodate.

Industry/Entity Type

Business

Requirements
Nice to have
• facial features so prospective client clearly identifies what type of business this is. Not stuffy or boring "spa" looking graphics. I am focusing just on face, body, waxing, eyelashes. No massage or nails.

```html
<!DOCTYPE html>
<html lang="en">
<head>
<meta charset="utf-8">
<title>Glow Haven by Marisol – Business Card</title>
<link rel="stylesheet" href="https://fonts.googleapis.com/css2?family=Jost:wght@400&family=Oswald:wght@400;500&family=Mrs+Saint+Delafield&family=Archivo+Narrow:wght@400&display=swap">
<style>
  :root {
    --stage: #ececec;
    --card-black: #141414;
    --card-paper: #f7f6f3;
    --ink: #1a1a1a;
    --brand-pink: #e0559f;
    --wordmark: #e58cc0;
    --art-blue: #3f9fd0;
    --art-pink: #e893c0;
    --art-pale: #dfe9f1;
  }
  * { margin: 0; padding: 0; box-sizing: border-box; }
  html, body {
    width: 1200px;
    height: 1200px;
    overflow: hidden;
    background: var(--stage);
  }
  .canvas {
    width: 1200px;
    height: 1200px;
    display: flex;
    flex-direction: column;
    align-items: center;
    justify-content: center;
    gap: 40px;
  }
  .card {
    width: 940px;
    height: 537px;
    position: relative;
    overflow: hidden;
    box-shadow: 0 6px 24px rgba(0,0,0,0.12);
  }

  /* Front */
  .card-front {
    background: var(--card-black);
    display: flex;
    flex-direction: column;
    align-items: center;
    justify-content: center;
  }
  .wordmark {
    font-family: "Jost", sans-serif;
    font-weight: 400;
    color: var(--wordmark);
    text-align: center;
    line-height: 1;
  }
  .wordmark-name {
    font-size: 78px;
    letter-spacing: 3px;
    text-transform: uppercase;
  }
  .wordmark-by {
    margin-top: 10px;
    font-size: 36px;
    letter-spacing: 1px;
  }

  /* Back */
  .card-back {
    background: var(--card-paper);
  }
  .portrait-art {
    position: absolute;
    left: 0;
    top: 0;
    width: 370px;
    height: 100%;
    background:
      radial-gradient(ellipse at 30% 25%, var(--art-blue) 0%, rgba(63,159,208,0) 55%),
      radial-gradient(ellipse at 15% 60%, var(--art-pink) 0%, rgba(232,147,192,0) 50%),
      linear-gradient(90deg, var(--art-pale) 0%, rgba(223,233,241,0.6) 70%, rgba(247,246,243,0) 100%);
  }
  .card-text {
    position: absolute;
    right: 44px;
    top: 0;
    height: 100%;
    text-align: right;
    color: var(--ink);
  }
  .tagline {
    margin-top: 62px;
    font-family: "Oswald", sans-serif;
    font-weight: 400;
    font-size: 28px;
    letter-spacing: 0.5px;
    text-transform: uppercase;
  }
  .tagline .accent { color: var(--brand-pink); }
  .specialty {
    margin-top: 4px;
    font-family: "Oswald", sans-serif;
    font-size: 20px;
    letter-spacing: 0.5px;
    text-transform: uppercase;
  }
  .signature {
    margin-top: 60px;
    margin-right: 40px;
    font-family: "Mrs Saint Delafield", cursive;
    font-size: 96px;
    line-height: 1;
  }
  .title {
    margin-top: 6px;
    margin-right: 40px;
    font-family: "Oswald", sans-serif;
    font-weight: 500;
    font-size: 20px;
    letter-spacing: 0.4px;
    text-transform: uppercase;
  }
  .contact {
    margin-top: 54px;
    font-family: "Archivo Narrow", sans-serif;
    font-size: 31px;
    line-height: 1.25;
    list-style: none;
  }
</style>
</head>
<body>
<main class="canvas">
  <section class="card card-front" aria-label="Card front">
    <div class="wordmark">
      <div class="wordmark-name">Glow Haven</div>
      <div class="wordmark-by">by marisol</div>
    </div>
  </section>

  <section class="card card-back" aria-label="Card back">
    <div class="portrait-art" role="img" aria-label="Watercolour illustration of a woman's face in profile in blue and pink tones"></div>
    <div class="card-text">
      <p class="tagline">Unique and affordable skin care just for <span class="accent">you</span></p>
      <p class="specialty">Specializing in Lumera Skin Care Products</p>
      <p class="signature">Marisol Vega</p>
      <p class="title">Professional Licensed Esthetician</p>
      <ul class="contact">
        <li>1418 Cedar Lane Ashford, CO 80612</li>
        <li>555-014-2287</li>
        <li>glowhavenbymarisol.com</li>
      </ul>
    </div>
  </section>
</main>
</body>
</html>
```